Corporate Business Card

Very professional, Modern, Not to busy, include phone address email, website
(555) 617-4930, 18761 52nd Avenue S, Alder Falls, OR 98047, martin@plumlinegroup.com, varkoworks.com

Target Market(s)

Manufacturing

Industry/Entity Type

Aero, machining, manufacturing, Off road racing

Contact Information for Business Card

Phone, address email, website

```html
<!DOCTYPE html>
<html lang="en">
<head>
<meta charset="utf-8">
<title>Varko Works – Business Card</title>
<link rel="stylesheet" href="https://fonts.googleapis.com/css2?family=Orbitron:wght@700&family=Roboto:wght@400;700&display=swap">
<style>
  :root {
    --page-bg: #e9e9eb;
    --navy: #2a3767;
    --navy-deep: #222d58;
    --navy-light: #34437a;
    --red: #c11f24;
    --white: #ffffff;
    --text-light: #eef0f6;
  }
  * { box-sizing: border-box; margin: 0; padding: 0; }
  html, body {
    width: 1200px; height: 1138px; overflow: hidden;
    background: var(--page-bg);
  }
  .canvas { position: relative; width: 1200px; height: 1138px; }

  .card {
    position: absolute;
    left: 276px;
    width: 620px;
    height: 375px;
    border-radius: 16px;
    overflow: hidden;
    background: linear-gradient(180deg, var(--navy) 0%, var(--navy-deep) 100%);
  }
  .card--front { top: 186px; }
  .card--back  { top: 608px; }

  /* Front */
  .front-pattern {
    position: absolute; inset: 0;
    background: linear-gradient(135deg, var(--navy-light) 0%, var(--navy) 50%, var(--navy-deep) 100%);
  }
  .front-wordmark {
    position: absolute;
    left: 54px; top: 286px;
    font-family: "Roboto", sans-serif;
    font-weight: 700;
    font-size: 34px;
    line-height: 40px;
    letter-spacing: 1px;
    color: var(--white);
  }

  /* Back */
  .back-shape { position: absolute; inset: 0; }
  .contact { position: absolute; left: 66px; top: 104px; }
  .contact__name {
    font-family: "Orbitron", sans-serif;
    font-weight: 700;
    font-size: 22px;
    line-height: 28px;
    letter-spacing: 0.5px;
    color: var(--white);
    margin-bottom: 16px;
  }
  .contact__name .surname { color: var(--red); }
  .contact__list { list-style: none; }
  .contact__item {
    position: relative;
    padding-left: 32px;
    font-family: "Roboto", sans-serif;
    font-size: 16px;
    line-height: 24.4px;
    color: var(--text-light);
    white-space: nowrap;
  }
  .contact__icon {
    position: absolute; left: 6px; top: 5px;
    width: 14px; height: 14px;
  }
  .back-wordmark {
    position: absolute;
    left: 516px; top: 186px;
    transform: translate(-50%, -50%) rotate(-90deg);
    white-space: nowrap;
    font-family: "Roboto", sans-serif;
    font-weight: 700;
    font-size: 36px;
    line-height: 42px;
    letter-spacing: 1px;
    color: var(--white);
  }
</style>
</head>
<body>
<main class="canvas">

  <section class="card card--front" aria-label="Business card front">
    <div class="front-pattern" role="img" aria-label="Tone-on-tone embossed repeating company name pattern"></div>
    <p class="front-wordmark">VARKO WORKS</p>
  </section>

  <section class="card card--back" aria-label="Business card back">
    <svg class="back-shape" viewBox="0 0 620 375" width="620" height="375" aria-hidden="true">
      <path d="M455 0 Q352 195 462 375 L620 375 L620 0 Z" fill="var(--white)"/>
      <path d="M461 0 Q360 190 468 375 L620 375 L620 0 Z" fill="var(--red)"/>
    </svg>

    <div class="contact">
      <h1 class="contact__name">DANIEL <span class="surname">HARLOW</span></h1>
      <ul class="contact__list">
        <li class="contact__item">
          <svg class="contact__icon" viewBox="0 0 14 14"><path d="M1 4 Q7 0 13 4 L11 6 L9 5 L9 4 Q7 3 5 4 L5 5 L3 6 Z M3 7 L11 7 L12 12 L2 12 Z" fill="var(--red)"/></svg>
          (555) 617-4930
        </li>
        <li class="contact__item">
          <svg class="contact__icon" viewBox="0 0 14 14"><rect x="1" y="3" width="12" height="9" fill="var(--red)"/><path d="M1 3 L7 8 L13 3" stroke="var(--navy)" stroke-width="1.2" fill="none"/></svg>
          martin@plumlinegroup.com
        </li>
        <li class="contact__item">
          <svg class="contact__icon" viewBox="0 0 14 14"><path d="M7 14 C3 9 2 7 2 5 A5 5 0 0 1 12 5 C12 7 11 9 7 14 Z" fill="var(--red)"/><circle cx="7" cy="5" r="2" fill="var(--navy)"/></svg>
          18761 52nd Avenue S,<br>Alder Falls, OR 98047
        </li>
        <li class="contact__item">
          <svg class="contact__icon" viewBox="0 0 14 14"><circle cx="7" cy="7" r="6" fill="var(--red)"/><path d="M1 7 H13 M7 1 V13 M7 1 Q3 7 7 13 M7 1 Q11 7 7 13" stroke="var(--navy)" stroke-width="0.8" fill="none"/></svg>
          www.varkoworks.com
        </li>
      </ul>
    </div>

    <p class="back-wordmark">VARKO WORKS</p>
  </section>

</main>
</body>
</html>
```